Grovecraft Lip Balm. It is formulated with men in mind but other people certainly can use it.

The over arching name of the project is Tharn - which needs to be in the label somewhere, but Grovecraft is the title.
It would be for a round jar container.
It is out of promoting products for men to open discussion about health issues that men often not talk about. As each product is created it will have a message to men about the health issue and where to find information, seek help or just be able to talk about it.
I would like darker colours (black) as the base but using other colours to
for the wording and design.
I am open to ideas on the layout, I have included some ideas, and also some of my own labelling ideas that I have worked on. I do like the carbon fibre background look that I have for my tharn label. I have also included my wevnu label with some colour ideas.
I also was wondering about making it a after tattoo balm so that it can also be used as a lip balm as well…two for the price of one..basically the same ingredients are used.
They may change the look of the intended artwork..but I leave it in your skill full hands.
My number is +61498152073. You can txt me if you need some clarification.
Thank you
Kind regards and blessings

Target Market(s)

Target market is men of all ages as they can all be affected by one health issue or another at different times of life

Industry/Entity Type

Healthcare and beauty

Font styles to use
Sans Serif
Decorative

Requirements
Must have
• I still need to indeed to ingredients and container size.
Nice to have
• A novel and different look from the usual crowd that try to hard to look cool or funky

```html
<!DOCTYPE html>
<html lang="en">
<head>
<meta charset="utf-8">
<title>Tharn Grovecraft Lip Balm – Jar Label</title>
<link rel="stylesheet" href="https://fonts.googleapis.com/css2?family=Oswald:wght@500&family=Lato:wght@400;700&display=swap">
<style>
  :root {
    --backdrop: #d5d9dc;
    --jar-black: #0b0b0c;
    --jar-charcoal: #1a1a1c;
    --accent-blue: #1ea3e6;
    --silver: #c9ccd0;
    --silver-dark: #8e9297;
    --muted-text: #b9bcc0;
  }
  * { box-sizing: border-box; margin: 0; padding: 0; }
  html, body { width: 1200px; height: 900px; overflow: hidden; }
  body {
    background: var(--backdrop);
    position: relative;
    font-family: "Lato", sans-serif;
  }

  /* Wrap-around jar label, laid flat */
  .jar-label {
    position: absolute;
    left: 110px;
    top: 190px;
    width: 560px;
    height: 520px;
    background: var(--jar-black);
  }
  .lid-band {
    height: 130px;
    background: linear-gradient(180deg, #050505 0%, var(--jar-charcoal) 100%);
  }
  .accent-rule {
    height: 5px;
    background: var(--accent-blue);
  }
  .accent-rule--thin {
    height: 2px;
    margin-top: 4px;
    background: var(--silver-dark);
  }
  .label-body {
    position: relative;
    height: 379px;
    background: radial-gradient(ellipse at 50% 35%, #1c1c1f 0%, var(--jar-black) 70%);
    text-align: center;
    padding-top: 36px;
  }
  .brand-name {
    font-family: "Lato", sans-serif;
    font-weight: 700;
    font-size: 30px;
    letter-spacing: 4px;
    color: var(--silver);
  }
  .product-title {
    font-family: "Oswald", sans-serif;
    font-weight: 500;
    font-size: 64px;
    line-height: 1;
    margin-top: 12px;
    color: var(--accent-blue);
    letter-spacing: 1px;
  }
  .product-type {
    font-size: 11px;
    letter-spacing: 4px;
    color: var(--muted-text);
    margin-top: 10px;
  }
  .benefit-badges {
    display: flex;
    justify-content: center;
    gap: 40px;
    margin-top: 32px;
  }
  .benefit-badge { width: 62px; height: 62px; }
  .benefit-badge text {
    font-family: "Lato", sans-serif;
    font-size: 5px;
    fill: var(--muted-text);
    text-anchor: middle;
  }
  .volume-tab {
    position: absolute;
    left: 50%;
    bottom: 10px;
    transform: translateX(-50%);
    background: var(--accent-blue);
    color: #06141c;
    font-family: "Lato", sans-serif;
    font-weight: 700;
    font-size: 13px;
    padding: 5px 10px 4px;
    border-radius: 7px 7px 0 0;
  }
  .base-rule {
    position: absolute;
    left: 0; right: 0; bottom: 0;
    height: 10px;
    background: linear-gradient(180deg, var(--silver) 0 50%, var(--accent-blue) 50% 100%);
  }

  /* Jar lid top */
  .jar-lid {
    position: absolute;
    left: 705px;
    top: 195px;
    width: 510px;
    height: 510px;
    border-radius: 50%;
    background: var(--jar-black);
    display: flex;
    align-items: center;
    justify-content: center;
  }
  .lid-brand {
    font-family: "Lato", sans-serif;
    font-weight: 700;
    font-size: 52px;
    letter-spacing: 6px;
    color: var(--silver);
    margin-top: -4px;
  }
</style>
</head>
<body>

<section class="jar-label">
  <div class="lid-band"></div>
  <div class="accent-rule"></div>
  <div class="accent-rule--thin"></div>
  <div class="label-body">
    <p class="brand-name">THARN</p>
    <h1 class="product-title">GROVECRAFT</h1>
    <p class="product-type">LIP BALM</p>

    <div class="benefit-badges">
      <svg class="benefit-badge" viewBox="0 0 62 62" aria-label="Cruelty free">
        <polygon points="16,4 46,4 60,31 46,58 16,58 2,31" fill="none" stroke="#1ea3e6" stroke-width="1.6"/>
        <circle cx="31" cy="26" r="7" fill="#1ea3e6"/>
        <text x="31" y="42">CRUELTY</text>
        <text x="31" y="48">FREE</text>
      </svg>
      <svg class="benefit-badge" viewBox="0 0 62 62" aria-label="Moisturizing">
        <polygon points="16,4 46,4 60,31 46,58 16,58 2,31" fill="none" stroke="#1ea3e6" stroke-width="1.6"/>
        <path d="M31 15 C27 22 25 25 25 28 A6 6 0 0 0 37 28 C37 25 35 22 31 15 Z" fill="#1ea3e6"/>
        <path d="M22 34 Q31 40 40 34" fill="none" stroke="#1ea3e6" stroke-width="1.2"/>
        <text x="31" y="46">MOISTURIZING</text>
      </svg>
      <svg class="benefit-badge" viewBox="0 0 62 62" aria-label="100 percent natural">
        <polygon points="16,4 46,4 60,31 46,58 16,58 2,31" fill="none" stroke="#1ea3e6" stroke-width="1.6"/>
        <path d="M30 34 C22 32 20 24 22 18 C28 20 32 26 30 34 Z" fill="#1ea3e6"/>
        <path d="M32 34 C34 26 38 22 43 21 C43 28 39 33 32 34 Z" fill="#1ea3e6"/>
        <text x="31" y="42">100 %</text>
        <text x="31" y="48">NATURAL</text>
      </svg>
    </div>

    <span class="volume-tab">50ML</span>
    <div class="base-rule"></div>
  </div>
</section>

<section class="jar-lid">
  <p class="lid-brand">THARN</p>
</section>

</body>
</html>
```